Business Card Design Project

I need a business card designed from scratch. I have an existing logo that I can upload in Illustrator for modification or redesign.

The Company is called Query Lanterns http://querylanterns.com.au and we provide Search Engine Optimization services to Australian businesses. The current logo signifies an increase in visitors, profits etc...

There are no restrictions as to the redesign - colours, style etc are all open to change.

Cards will be full colour and one sided printed at http://www.cardmoxel.com.au so check their requirements for file format and sizes etc.

I will expect all original files upon completion of project.

Target Market(s)

Any business with a web site looking to improve their search engine rankings

Industry/Entity Type

Business

Requirements
Must have
• I like modern, sleek designs. Clean, not fussy, uncluttered.

```html
<!DOCTYPE html>
<html lang="en">
<head>
<meta charset="utf-8">
<title>Query Lanterns – Business Card</title>
<link rel="stylesheet" href="https://fonts.googleapis.com/css2?family=Source+Sans+3:wght@400;600;700&display=swap">
<style>
  :root {
    --backdrop: #4a2e1c;
    --card: #ffffff;
    --brand-blue: #1a6fb5;
    --brand-yellow: #f2c21b;
    --ink: #3a3a3a;
    --ink-soft: #555555;
    --rule: #c9c9c9;
  }
  * { box-sizing: border-box; margin: 0; padding: 0; }
  html, body { width: 1200px; height: 412px; overflow: hidden; }
  body {
    background: var(--backdrop);
    font-family: "Source Sans 3", "Myriad Pro", Arial, sans-serif;
    color: var(--ink);
    position: relative;
  }
  .card {
    position: absolute;
    top: 65px;
    width: 496px;
    height: 283px;
    background: var(--card);
    box-shadow: 0 4px 12px rgba(0,0,0,0.45);
  }
  .card--front { left: 73px; }
  .card--back { left: 631px; }

  .brand {
    display: flex;
    align-items: center;
    gap: 8px;
    color: var(--brand-blue);
    font-weight: 700;
    white-space: nowrap;
  }
  .brand__dot {
    border-radius: 50%;
    background: var(--brand-yellow);
    flex: none;
  }
  .card--front .brand {
    position: absolute;
    left: 30px;
    top: 126px;
    font-size: 26px;
  }
  .card--front .brand__dot { width: 14px; height: 14px; }

  .divider {
    position: absolute;
    left: 262px;
    top: 71px;
    width: 1px;
    height: 143px;
    background: linear-gradient(to bottom, transparent, var(--rule) 20%, var(--rule) 80%, transparent);
  }
  .details {
    position: absolute;
    left: 288px;
    top: 74px;
    font-size: 12.5px;
    color: var(--ink);
  }
  .details__name {
    font-size: 16.5px;
    font-weight: 700;
    margin-bottom: 12px;
  }
  .details__title { font-weight: 400; font-size: 13px; }
  .contact-list { list-style: none; }
  .contact-list li {
    display: flex;
    align-items: center;
    gap: 6px;
    height: 17px;
  }
  .contact-list svg { width: 10px; height: 10px; fill: var(--ink); flex: none; }
  .address { margin-top: 8px; line-height: 17px; font-size: 13px; }

  .card--back .brand {
    position: absolute;
    left: 0;
    right: 0;
    top: 92px;
    justify-content: center;
    font-size: 40px;
    gap: 12px;
  }
  .card--back .brand__dot { width: 22px; height: 22px; }
  .web-line {
    position: absolute;
    left: 0;
    right: 0;
    top: 232px;
    text-align: center;
    font-size: 12px;
    font-weight: 700;
    letter-spacing: 4.2px;
    color: var(--ink-soft);
  }
</style>
</head>
<body>
  <section class="card card--front">
    <div class="brand"><span class="brand__dot"></span>Query Lanterns</div>
    <div class="divider"></div>
    <div class="details">
      <p class="details__name">Your Name / <span class="details__title">Title</span></p>
      <ul class="contact-list">
        <li><svg viewBox="0 0 10 10"><path d="M2 0.5 L3.6 0.5 L4.3 3 L3.2 3.8 Q4 5.8 6.2 6.8 L7 5.7 L9.5 6.4 L9.5 8 Q9.5 9.5 8 9.5 Q0.5 8.5 0.5 2 Q0.5 0.5 2 0.5Z"/></svg>091 234 5678</li>
        <li><svg viewBox="0 0 10 10"><path d="M3 0 H7 Q8 0 8 1 V9 Q8 10 7 10 H3 Q2 10 2 9 V1 Q2 0 3 0Z M3 1.5 V7 H7 V1.5Z"/></svg>091 234 5678</li>
        <li><svg viewBox="0 0 10 10"><path d="M0 2 H10 V8.5 H0Z M0.8 2.6 L5 5.6 L9.2 2.6" fill="none" stroke="#3a3a3a" stroke-width="1.2"/></svg>enquiry@querylanterns.com.au</li>
        <li><svg viewBox="0 0 10 10"><circle cx="5" cy="5" r="4.6"/><path d="M0.6 5 H9.4 M5 0.4 Q2.5 5 5 9.6 M5 0.4 Q7.5 5 5 9.6" stroke="#fff" stroke-width="0.7" fill="none"/></svg>www.querylanterns.com.au</li>
      </ul>
      <p class="address">Complex name, Street name<br>City, State, zip code</p>
    </div>
  </section>

  <section class="card card--back">
    <div class="brand"><span class="brand__dot"></span>Query Lanterns</div>
    <p class="web-line">www.querylanterns.com.au</p>
  </section>
</body>
</html>
```